Where's my Gym Buddy? looking to do two promotions as listed in project description

looking for two designs.

1: selfie frame design!! (wording) Icebound Hustle Gala, my Summer fitness has started, Tag a friend who should be joining me. T.C Tag your posts to @kestrelhubsydney to win points for the competition. (Snow graphic) in a selfie frame design. this needs to be the same design but across different departments as seen at the top of the photo's I've attached EG: #kestrelhubfitness #kestrelhubindoor #kestrelhubswim #kestrelhubwyong

2: Selfie Frame Design!! (Wording) Where's my gym buddy?, Tag a friend who should be at the gym, T.C.Tag your posts to @kestrelhubsydney to win points for the competition. Mister Plumtree Feel Selfie frame design

Target Market(s)

Gym Members

Industry/Entity Type

Gym

Colors

Designer to choose colors to be used in the design.

Requirements
Must have
• quirky and funky design, must include wording listed, must be a selfie frame design
Should not have
• whilst we are a big corporate gym, we pride ourselves on having really funky advertisements, so please no boring business corporate typical designs

```html
<!DOCTYPE html>
<html lang="en">
<head>
<meta charset="utf-8">
<title>Icebound Hustle Gala – Selfie Frame</title>
<link rel="stylesheet" href="https://fonts.googleapis.com/css2?family=Lobster&family=Saira+Condensed:wght@500&family=Share+Tech+Mono&display=swap">
<style>
  :root {
    --canvas-bg: #e9ecef;
    --ice-blue: #2f86b5;
    --ice-blue-light: #5fa9cf;
    --ice-blue-deep: #23739f;
    --fest-red: #ec3b36;
    --snow-white: #ffffff;
    --frame-edge: #c9ced3;
  }
  * { box-sizing: border-box; margin: 0; padding: 0; }
  html, body {
    width: 1200px;
    height: 900px;
    overflow: hidden;
    background: var(--canvas-bg);
  }
  .selfie-poster {
    position: absolute;
    left: 350px;
    top: 20px;
    width: 500px;
    height: 860px;
    overflow: hidden;
    box-shadow: 0 8px 24px rgba(0,0,0,0.18);
  }
  .snow-backdrop {
    position: absolute;
    inset: 0;
    background:
      radial-gradient(ellipse at 20% 8%, var(--ice-blue-light) 0%, transparent 40%),
      radial-gradient(ellipse at 85% 75%, var(--ice-blue-light) 0%, transparent 35%),
      linear-gradient(160deg, var(--ice-blue) 0%, var(--ice-blue-deep) 100%);
  }
  .festival-title {
    position: absolute;
    top: 52px;
    left: 0;
    width: 100%;
    text-align: center;
    font-family: "Lobster", cursive;
    font-weight: 400;
    font-size: 54px;
    line-height: 64px;
    color: var(--fest-red);
    letter-spacing: -1px;
    transform: rotate(-1deg);
    -webkit-text-stroke: 2px var(--snow-white);
    paint-order: stroke fill;
    text-shadow: 3px 3px 0 var(--snow-white), 5px 6px 8px rgba(0,0,0,0.3);
  }
  .tagline-band {
    position: absolute;
    top: 145px;
    left: 0;
    width: 100%;
    height: 48px;
    background: var(--fest-red);
    color: var(--snow-white);
    font-family: "Saira Condensed", sans-serif;
    font-weight: 500;
    font-size: 31px;
    line-height: 48px;
    text-align: center;
    letter-spacing: 1px;
    text-transform: uppercase;
  }
  .photo-window {
    position: absolute;
    top: 208px;
    left: 58px;
    width: 392px;
    height: 460px;
    background: var(--snow-white);
    border: 5px solid var(--frame-edge);
    box-shadow: inset 0 0 12px rgba(0,0,0,0.18), 0 2px 6px rgba(0,0,0,0.25);
    transform: rotate(1.5deg);
  }
  .footer-art {
    position: absolute;
    left: 0;
    top: 0;
  }
  .footer-text {
    font-family: "Share Tech Mono", monospace;
    font-size: 21px;
  }
  .call-to-tag { fill: var(--fest-red); }
  .terms-note { fill: var(--snow-white); }
</style>
</head>
<body>
  <main class="selfie-poster">
    <div class="snow-backdrop" role="img" aria-label="Blue wintry background scattered with white snowflakes and falling snow"></div>

    <h1 class="festival-title">Icebound Hustle Gala</h1>
    <p class="tagline-band">My Summer Fitness Has Started</p>

    <div class="photo-window" aria-label="Selfie opening"></div>

    <svg class="footer-art" width="500" height="860" viewBox="0 0 500 860">
      <polygon points="0,713 500,649 500,692 0,756" fill="var(--snow-white)"/>
      <polygon points="0,756 500,692 500,800 0,864" fill="var(--fest-red)"/>
      <g transform="rotate(-7.3 250 720)">
        <text class="footer-text call-to-tag" x="250" y="711" text-anchor="middle">Tag a friend who should be joining me.</text>
        <text class="footer-text terms-note" x="250" y="768" text-anchor="middle">T.C Tag your posts to @kestrelhubsydney</text>
        <text class="footer-text terms-note" x="262" y="794" text-anchor="middle">to win points for the competition.</text>
      </g>
    </svg>
  </main>
</body>
</html>
```